Web Developer Needs a Business Card Design

I need a personal business card design that represents me as a web developer for potential employers. I would like the background to be a dark color on the front for contrast with my logo and name. The back will have all my information along with a smaller version of the logo. I want something with a modern look and feel, not too conservative. This will be used for potential employers and freelance work.

Industry/Entity Type

Business

Contact Information for Business Card

Front should have my logo and name. The back should have all my personal information which would include: name: Tom Varulek, phone: 570-614-3098, email: tomvarulek@quillbox.net, website url: www.tomvarulek.net, logo, web developer.

Font styles to use
Sans Serif

Requirements
Must have
• Must include my logo. The color palette base color will be the logo color.

```html
<!DOCTYPE html>
<html lang="en">
<head>
<meta charset="utf-8">
<title>Tom Varulek — Business Card</title>
<link rel="stylesheet" href="https://fonts.googleapis.com/css2?family=Open+Sans:wght@400;600&display=swap">
<style>
  :root {
    --teal: #66c2ad;
    --teal-deep: #5bb8a3;
    --paper: #f7f7f5;
    --ink: #1c1c1c;
    --backdrop: #e4e1dc;
  }
  * { margin: 0; padding: 0; box-sizing: border-box; }
  html, body { width: 1200px; height: 892px; overflow: hidden; }
  body {
    background: var(--backdrop);
    font-family: "Open Sans", sans-serif;
    position: relative;
  }
  .card {
    position: absolute;
    top: 297px;
    width: 520px;
    height: 298px;
    overflow: hidden;
    box-shadow: 0 6px 18px rgba(0,0,0,0.18);
  }
  /* Front */
  .card-front {
    left: 40px;
    background: var(--teal);
    color: #fff;
  }
  .card-front .mark {
    position: absolute;
    left: 190px; top: 38px;
    width: 140px; height: 140px;
    border: 9px solid #fff;
    border-radius: 50%;
    display: flex; align-items: center; justify-content: center;
    font-weight: 600;
    font-size: 22px;
    color: #fff;
  }
  .card-front .name {
    position: absolute;
    left: 0; right: 0; top: 200px;
    text-align: center;
    font-weight: 400;
    font-size: 46px;
    letter-spacing: 0.5px;
  }
  /* Back */
  .card-back {
    left: 640px;
    background: var(--paper);
    color: var(--ink);
  }
  .card-back .band {
    position: absolute;
    left: 78px; right: 0; top: 0;
    height: 112px;
    background: var(--teal);
  }
  .card-back .mark {
    position: absolute;
    left: 200px; top: 22px;
    width: 120px; height: 120px;
    border-radius: 50%;
    background: var(--paper);
    display: flex; align-items: center; justify-content: center;
  }
  .card-back .mark span {
    width: 96px; height: 96px;
    border: 7px solid var(--teal);
    border-radius: 50%;
    display: flex; align-items: center; justify-content: center;
    font-weight: 600;
    font-size: 15px;
    color: var(--teal);
  }
  .card-back .identity {
    position: absolute;
    left: 26px; top: 176px;
    width: 220px;
    text-align: right;
  }
  .card-back .identity .name {
    font-size: 27px;
    font-weight: 400;
    color: var(--teal);
    line-height: 1.1;
  }
  .card-back .identity .role {
    font-size: 16px;
    margin-top: 2px;
  }
  .card-back .divider {
    position: absolute;
    left: 260px; top: 166px;
    width: 1.5px; height: 100px;
    background: var(--ink);
  }
  .card-back .contacts {
    position: absolute;
    left: 276px; top: 168px;
    list-style: none;
    font-size: 15.5px;
    line-height: 30px;
  }
  .card-back .contacts li { display: flex; align-items: center; gap: 9px; }
  .card-back .contacts svg { width: 13px; height: 13px; flex: none; }
</style>
</head>
<body>
  <section class="card card-front" aria-label="Card front">
    <div class="mark">Varulek</div>
    <div class="name">Tom Varulek</div>
  </section>

  <section class="card card-back" aria-label="Card back">
    <div class="band"></div>
    <div class="mark"><span>Varulek</span></div>
    <div class="identity">
      <div class="name">Tom Varulek</div>
      <div class="role">web developer</div>
    </div>
    <div class="divider"></div>
    <ul class="contacts">
      <li>
        <svg viewBox="0 0 13 13" aria-hidden="true"><rect width="13" height="13" fill="#66c2ad"/><path d="M4 3.2l1.4 1.6-.8.9c.5 1 1.3 1.8 2.3 2.3l.9-.8 1.6 1.4-.9 1.2C6 9.6 3.4 7 3 4.1z" fill="#fff"/></svg>
        570-614-3098
      </li>
      <li>
        <svg viewBox="0 0 13 13" aria-hidden="true"><rect width="13" height="13" fill="#66c2ad"/><circle cx="6.5" cy="6.5" r="3.6" fill="none" stroke="#fff" stroke-width="1.1"/><path d="M2.9 6.5h7.2M6.5 2.9v7.2" stroke="#fff" stroke-width="0.9"/></svg>
        www.tomvarulek.net
      </li>
      <li>
        <svg viewBox="0 0 13 13" aria-hidden="true"><rect width="13" height="13" fill="#66c2ad"/><rect x="2.8" y="4" width="7.4" height="5" fill="none" stroke="#fff" stroke-width="1"/><path d="M2.8 4l3.7 2.8L10.2 4" fill="none" stroke="#fff" stroke-width="1"/></svg>
        tomvarulek@quillbox.net
      </li>
    </ul>
  </section>
</body>
</html>
```